Need Flyer for Our Real estate Agency

Need to run General Campaign for our agency with Start of New Year as our theme ..Must have an agent's picture on the DL..
Address:
27 / 486Brindle rd, Marsden VIC 3047
Ph:03 9412 7306
email:info@kovalinrealestate.com.au
www.kovalinrealestate.com.au
Something like as attached picture..
Target Market(s)
Home Buyers
Industry/Entity Type
Real Estate Agent
Requirements
Must have
- Our Logo Colours

```html
<!DOCTYPE html>
<html lang="en">
<head>
<meta charset="utf-8">
<title>Kovalin Real Estate – New Year DL Flyer</title>
<link rel="stylesheet" href="https://fonts.googleapis.com/css2?family=Lato:wght@300;400;700;900&display=swap">
<style>
  :root {
    --navy: #14285e;
    --navy-deep: #0b1a45;
    --navy-light: #1f3a80;
    --maroon: #7a1420;
    --silver: #d2d3d6;
    --white: #ffffff;
    --page: #e9e9ea;
  }
  * { box-sizing: border-box; margin: 0; padding: 0; }
  html, body { width: 1200px; height: 1200px; overflow: hidden; }
  body {
    background: var(--page);
    font-family: "Lato", Arial, sans-serif;
    color: var(--white);
    position: relative;
  }
  .flyer {
    position: absolute;
    left: 115px;
    width: 970px;
    height: 460px;
    overflow: hidden;
    box-shadow: 0 6px 18px rgba(0,0,0,.25);
    background: var(--navy);
  }
  .flyer--front { top: 100px; }
  .flyer--back { top: 640px; }

  .flyer__photo {
    position: absolute;
    left: 0; top: 0;
    width: 460px; height: 460px;
  }
  .flyer--front .flyer__photo {
    background: linear-gradient(180deg, #b7c6d9 0%, #cfc9bd 40%, #5f6a72 62%, #1d2a55 100%);
  }
  .flyer--back .flyer__photo {
    background: linear-gradient(160deg, #1f4652 0%, #2c5561 35%, #c98a74 55%, #d7dadc 75%, #244a56 100%);
  }
  .flyer__shapes {
    position: absolute;
    inset: 0;
    width: 970px; height: 460px;
  }

  .brand {
    position: absolute;
    left: 555px;
    width: 300px;
    top: 122px;
    display: flex;
    align-items: center;
    justify-content: center;
    gap: 12px;
    font-weight: 400;
    font-size: 50px;
    line-height: 56px;
    letter-spacing: 6px;
    color: var(--white);
  }
  .brand__mark {
    width: 12px; height: 12px;
    background: var(--white);
  }

  .pitch__headline {
    position: absolute;
    left: 500px; width: 410px;
    top: 212px;
    text-align: center;
    font-weight: 300;
    font-size: 30px;
    line-height: 46px;
  }
  .pitch__sub {
    position: absolute;
    left: 468px; width: 474px;
    top: 327px;
    text-align: center;
    font-weight: 400;
    font-size: 15.5px;
    line-height: 20px;
    text-transform: uppercase;
    white-space: nowrap;
  }
  .pitch__sub strong { font-weight: 900; }
  .pitch__cta {
    position: absolute;
    left: 524px; width: 362px;
    top: 372px; height: 46px;
    background: var(--white);
    border-radius: 23px;
    box-shadow: 0 3px 6px rgba(0,0,0,.3);
    display: flex;
    align-items: center;
    justify-content: center;
    gap: 8px;
    color: var(--maroon);
    font-weight: 900;
    font-size: 21px;
  }
  .pitch__cta svg { width: 20px; height: 20px; }
  .pitch__note {
    position: absolute;
    left: 520px; width: 370px;
    top: 427px;
    text-align: center;
    font-weight: 400;
    font-size: 17px;
    line-height: 22px;
  }

  .contacts {
    position: absolute;
    left: 586px;
    top: 226px;
    list-style: none;
  }
  .contacts__item {
    display: flex;
    align-items: center;
    gap: 14px;
    height: 41px;
    font-weight: 400;
    font-size: 18px;
  }
  .contacts__icon { width: 18px; height: 18px; flex: none; }
  .address {
    position: absolute;
    left: 470px; width: 470px;
    top: 416px;
    text-align: center;
    font-size: 18px;
    line-height: 24px;
    font-weight: 400;
  }
</style>
</head>
<body>

<svg width="0" height="0" style="position:absolute" aria-hidden="true">
  <defs>
    <linearGradient id="panel-fill" x1="0" y1="0" x2="1" y2="1">
      <stop offset="0" stop-color="#1f3a80"/>
      <stop offset=".6" stop-color="#14285e"/>
      <stop offset="1" stop-color="#0b1a45"/>
    </linearGradient>
    <clipPath id="panel-area">
      <path d="M389 0 Q477 230 389 460 L970 460 L970 0 Z"/>
    </clipPath>
  </defs>
</svg>

<section class="flyer flyer--front">
  <div class="flyer__photo" role="img" aria-label="Photo of agent Rohan Mehra in a navy suit standing in front of a two-storey family home at dusk"></div>
  <svg class="flyer__shapes" viewBox="0 0 970 460" aria-hidden="true">
    <path d="M284 0 Q490 230 372 460 L970 460 L970 0 Z" fill="#d2d3d6"/>
    <path d="M360 0 Q480 230 381 460 L970 460 L970 0 Z" fill="#ffffff"/>
    <path d="M389 0 Q477 230 389 460 L970 460 L970 0 Z" fill="url(#panel-fill)"/>
    <g clip-path="url(#panel-area)">
      <rect x="380" y="386" width="590" height="5" fill="#ffffff"/>
      <rect x="380" y="392" width="590" height="68" fill="#7a1420"/>
    </g>
  </svg>
  <div class="brand"><span class="brand__mark"></span>KOVALIN</div>
  <p class="pitch__headline">Curios to know what your<br>home is worth?</p>
  <p class="pitch__sub">Start of new year with <strong>Rohan Mehra</strong> and find out!</p>
  <div class="pitch__cta">CALL ME NOW!
    <svg viewBox="0 0 20 20"><circle cx="10" cy="10" r="8.6" fill="none" stroke="#7a1420" stroke-width="1.8"/><path d="M7 5.5l1.6 2.3-1 1.2c.7 1.4 1.6 2.3 3 3l1.2-1 2.3 1.6-.8 1.7c-3.4-.3-6.7-3.6-7-7z" fill="#7a1420"/></svg>
    03 9412 7306</div>
  <p class="pitch__note">For Free property Appraisal</p>
</section>

<section class="flyer flyer--back">
  <div class="flyer__photo" role="img" aria-label="Photo of two hands sheltering a small red model house"></div>
  <svg class="flyer__shapes" viewBox="0 0 970 460" aria-hidden="true">
    <path d="M284 0 Q490 230 372 460 L970 460 L970 0 Z" fill="#d2d3d6"/>
    <path d="M360 0 Q480 230 381 460 L970 460 L970 0 Z" fill="#ffffff"/>
    <path d="M389 0 Q477 230 389 460 L970 460 L970 0 Z" fill="url(#panel-fill)"/>
    <g clip-path="url(#panel-area)">
      <rect x="380" y="386" width="590" height="5" fill="#ffffff"/>
      <rect x="380" y="392" width="590" height="68" fill="#7a1420"/>
    </g>
  </svg>
  <div class="brand"><span class="brand__mark"></span>KOVALIN</div>
  <ul class="contacts">
    <li class="contacts__item">
      <svg class="contacts__icon" viewBox="0 0 20 20"><circle cx="10" cy="10" r="8.8" fill="none" stroke="#fff" stroke-width="1.5"/><path d="M7 5.5l1.6 2.3-1 1.2c.7 1.4 1.6 2.3 3 3l1.2-1 2.3 1.6-.8 1.7c-3.4-.3-6.7-3.6-7-7z" fill="#fff"/></svg>
      03 9412 7306</li>
    <li class="contacts__item">
      <svg class="contacts__icon" viewBox="0 0 20 20"><circle cx="10" cy="10" r="8.8" fill="none" stroke="#fff" stroke-width="1.5"/><rect x="5.5" y="7" width="9" height="6.5" fill="none" stroke="#fff" stroke-width="1.3"/><path d="M5.5 7l4.5 3.6L14.5 7" fill="none" stroke="#fff" stroke-width="1.3"/></svg>
      info@kovalinrealestate.com.au</li>
    <li class="contacts__item">
      <svg class="contacts__icon" viewBox="0 0 20 20"><circle cx="10" cy="10" r="8.8" fill="none" stroke="#fff" stroke-width="1.5"/><circle cx="10" cy="10" r="5" fill="none" stroke="#fff" stroke-width="1.1"/><ellipse cx="10" cy="10" rx="2.2" ry="5" fill="none" stroke="#fff" stroke-width="1.1"/><path d="M5 10h10" stroke="#fff" stroke-width="1.1"/></svg>
      www.kovalinrealestate.com.au</li>
  </ul>
  <p class="address">27 / 486Brindle rd, Marsden VIC 3047</p>
</section>

</body>
</html>
```